WP website design (Tarnwick)

We need a wordpress design for an established auction and real estate company based in Arkansas. The winning design will incorporate a professional color scheme with company logo in a clean layout. The design needs to consider that this will be developed on a responsive theme.

Industry/Entity Type

Real Estate

Font styles to use
Sans Serif

Colors

Designer to choose colors to be used in the design.

Requirements
Must have
• Site will have slideshow, please use stock real estate or other image. A rough idea of homepage content is attached - not necessarily for design purposes.

Navigation Structure is:
1) Home
2) Auctions
3) Services
4) For Sale
5) About Us
6) Ned Videos
7) News & Events
8) Contact Us

Widgets will include:
Social media icons (plain square, plain square, plain square)
Testimonials Widget - this should be prominent
Featured Video
Email Signup form (Sign up to receive exclusive email updates for Tarnwick auctions. )
Nice to have
• A drop down menu example
Should not have
• no gavel in the design

```html
<!DOCTYPE html>
<html lang="en">
<head>
<meta charset="utf-8">
<title>Tarnwick Auction &amp; Marketing</title>
<link rel="stylesheet" href="https://fonts.googleapis.com/css2?family=Open+Sans:ital,wght@0,400;0,600;0,700;1,400&family=Roboto+Condensed:wght@400;700&display=swap">
<style>
:root{
  --green:#0a8a3a;
  --green-dark:#06692b;
  --green-light:#18a14b;
  --ink:#2b2b2b;
  --muted:#666;
  --soft:#999;
  --line:#dcdcdc;
  --panel:#f4f4f4;
  --hero-bg:#e9e9e9;
  --orange:#ff8a00;
  --orange-light:#ffa31a;
  --olive:#c9d39a;
  --amber:#ffb400;
  --sky:#2bb6d8;
  --charcoal:#3a3a3a;
}
*{box-sizing:border-box;margin:0;padding:0}
html,body{width:872px;height:1200px;overflow:hidden}
body{position:relative;background:#fff;font-family:"Open Sans",sans-serif;color:var(--ink)}
.abs{position:absolute}

/* header */
.brand{left:76px;top:24px}
.brand-name{display:flex;align-items:center;gap:8px;font-size:34px;font-weight:700;color:#1d2a1f;letter-spacing:1px;line-height:36px;text-transform:uppercase}
.brand-dot{width:18px;height:18px;border-radius:50%;background:var(--green)}
.brand-sub{font-size:13px;font-weight:700;color:#1d2a1f;letter-spacing:1px;margin-left:10px}
.contact{right:78px;top:22px;text-align:right}
.contact-phone{font-size:20px;color:var(--green);line-height:26px}
.contact-name{font-size:11px;color:var(--ink);margin-top:4px}
.contact-note{font-size:10px;color:var(--muted)}

/* nav */
.nav{left:0;top:90px;width:872px;height:35px;background:linear-gradient(#19a04a,#077a31);border-bottom:1px solid #05602a}
.nav ul{list-style:none;display:flex;position:absolute;left:71px;top:0;height:35px}
.nav li{font-family:"Roboto Condensed",sans-serif;font-size:13px;color:#fff;line-height:35px;padding:0 16px;border-right:1px solid rgba(0,0,0,.15)}
.nav li:last-child{border-right:0}
.nav li.is-active{background:var(--green-dark);padding:0 17px}

/* hero */
.hero{left:0;top:125px;width:872px;height:271px;background:var(--hero-bg)}
.slider{left:73px;top:134px;width:519px;height:246px;border-radius:3px;background:linear-gradient(160deg,#6d7480 0%,#3d434c 40%,#bfb27c 70%,#6b6352 100%)}
.badge{left:61px;top:262px;width:187px;height:64px;background:linear-gradient(var(--orange-light),var(--orange));clip-path:polygon(0 0,100% 0,83% 100%,0 100%);color:#fff;padding:8px 0 0 23px}
.badge-fold{left:61px;top:326px;width:12px;height:10px;background:#b35a00;clip-path:polygon(0 0,100% 0,100% 100%)}
.badge-line{font-size:16px;line-height:18px}
.badge-price{font-size:22px;line-height:28px}
.badge-price b{font-weight:600}
.dots{left:310px;top:362px;display:flex;gap:3px}
.dots span{width:9px;height:9px;border-radius:50%;background:#eee}
.profile{left:598px;top:136px;width:201px;height:243px;background:#f4f4f4;border:1px solid #d6d6d6;border-radius:2px}
.profile-photo{width:199px;height:196px;background:linear-gradient(#6a6a6a,#2b2b2b)}
.profile-name{text-align:center;font-size:16px;margin-top:7px;line-height:18px}
.profile-role{text-align:center;font-size:10px;line-height:14px}

/* testimonials */
.card{background:#fff;border:1px solid var(--line);border-radius:3px}
.testimonial{left:73px;top:410px;width:519px;height:132px;background:linear-gradient(#fff,#f4f4f4);padding:12px 19px}
.section-title{font-size:14px;font-weight:600;color:var(--green);line-height:18px}
.testimonial-text{font-size:8.6px;font-style:italic;color:var(--muted);line-height:16.3px;margin-top:4px}
.testimonial-by{font-size:9px;color:var(--green);font-weight:600;margin-top:6px}
.video{left:598px;top:408px;width:202px;height:134px;padding:3px}
.video-frame{width:100%;height:100%;background:linear-gradient(120deg,#d9c7b3,#9a8f86 50%,#e8e6e4);display:flex;align-items:center;justify-content:center}

/* auctions */
.auctions{left:73px;top:551px;width:519px;height:550px;background:#fff;border:1px solid var(--line);border-radius:3px;overflow:hidden}
.auctions-head{height:37px;background:linear-gradient(#13984a,#077a31);color:#fff;font-size:14px;padding:0 19px;line-height:37px}
.lot{left:17px;width:483px;height:148px;background:#fff;box-shadow:0 1px 3px rgba(0,0,0,.18)}
.lot-head{height:26px;color:#fff;font-size:12px;font-weight:600;line-height:26px;padding-left:14px}
.lot-head.real{background:var(--olive)}
.lot-head.estate{background:var(--amber)}
.lot-head.auto{background:var(--sky)}
.lot-photo{position:absolute;left:12px;top:36px;width:130px;height:100px}
.lot-body{position:absolute;left:153px;top:37px;width:320px}
.lot-title{font-size:9.5px;color:var(--ink);line-height:14px}
.lot-meta{font-size:8.5px;color:var(--muted);line-height:18px}
.lot-meta b{font-weight:600;color:var(--ink)}
.lot-desc{font-size:8px;color:var(--soft);line-height:14.4px;margin-top:2px}
.more{position:absolute;left:0;bottom:0;width:519px;height:23px;background:var(--charcoal);color:#fff;font-size:9px;font-weight:700;text-align:center;line-height:23px}

/* sidebar */
.signup{left:599px;top:551px;width:200px;height:232px}
.side-head{height:34px;background:linear-gradient(#4a4a4a,#2f2f2f);color:#fff;font-size:13.5px;line-height:34px;padding-left:15px;border-radius:3px 3px 0 0}
.field{margin:11px 0 0 15px;width:172px;height:20px;border:1px solid #cfcfcf;background:linear-gradient(#f3f3f3,#fff);font-size:8.5px;color:var(--muted);line-height:18px;padding-left:8px}
.field+.field{margin-top:7px}
.field.tall{height:45px}
.submit{position:absolute;right:13px;top:200px;width:63px;height:22px;background:var(--green);color:#fff;font-size:9.5px;font-weight:700;text-align:center;line-height:22px;border-radius:2px}
.services{left:599px;top:791px;width:200px;height:232px}
.services-head{height:34px;background:linear-gradient(#fafafa,#ececec);font-size:13.5px;line-height:44px;padding-left:15px}
.services ul{list-style:none;margin:8px 19px 0 19px}
.services li{font-size:8.4px;color:var(--muted);line-height:17.7px;border-bottom:1px solid #e6e6e6;padding-left:10px;position:relative}
.services li:last-child{border-bottom:0}
.services li::before{content:"";position:absolute;left:1px;top:6px;border-left:3px solid #999;border-top:3px solid transparent;border-bottom:3px solid transparent}
.partners{left:601px;top:1042px;width:201px;height:62px;display:flex;align-items:center;justify-content:space-around;padding:0 10px}
.partner{height:18px;border-radius:3px;background:#c9d3dc}

/* footer */
.footer{left:0;top:1126px;width:872px;height:74px;background:linear-gradient(#e8e8e8,#fff 40%)}
.footer-links{left:78px;top:1144px;font-size:10px;color:var(--muted)}
.footer-links span{margin:0 5px}
.footer-copy{left:78px;top:1166px;font-size:8.2px;color:var(--muted)}
.social{left:730px;top:1142px;display:flex;gap:5px}
.social span{width:18px;height:18px;border-radius:2px}
</style>
</head>
<body>

<header>
  <div class="abs brand">
    <div class="brand-name"><span>Tarnwick</span><span class="brand-dot"></span></div>
    <div class="brand-sub">Auction &amp; Marketing, LLC</div>
  </div>
  <div class="abs contact">
    <div class="contact-phone">1-800-555-0142</div>
    <div class="contact-name">Dale Everly</div>
    <div class="contact-note">Etiam est nunc venenatis in tristique</div>
  </div>
</header>

<nav class="abs nav">
  <ul>
    <li class="is-active">HOME</li>
    <li>AUCTIONS</li>
    <li>SERVICES</li>
    <li>FOR SALE</li>
    <li>ABOUT US</li>
    <li>NED VIDEOS</li>
    <li>NEWS &amp; EVENTS</li>
    <li>CONTACT US</li>
  </ul>
</nav>

<section class="abs hero"></section>
<div class="abs slider" role="img" aria-label="Classic cars on display in an auction hall"></div>
<div class="abs badge">
  <div class="badge-line">Available Now</div>
  <div class="badge-price">Lot <b>$250</b></div>
</div>
<div class="abs badge-fold"></div>
<div class="abs dots"><span></span><span></span><span></span><span></span></div>
<div class="abs profile">
  <div class="profile-photo" role="img" aria-label="Portrait of auctioneer Glen Hartley"></div>
  <div class="profile-name">Glen Hartley</div>
  <div class="profile-role">Integer orci tellus consequat</div>
</div>

<section class="abs card testimonial">
  <h2 class="section-title">CUSTOMER TESTIMONIALS</h2>
  <p class="testimonial-text">Vivamus porttitor g purus nisi eleifend libero a tempus libero lectus feugiat felis. Morbi diam mauris viverra in gravida eu mattis in ante. Morbi eget arcu. Morbi porta libero id ullamcorper nonummy nibh ligula pulvinar metus eget consectetuer augue nisi quis lacus. Ut ac mi quis lacus mollis aliquam. Curabitur iaculis tempus eros. Curabitur vel mi sit amet magna malesuada ultrices</p>
  <p class="testimonial-by">By Marcus Pell</p>
</section>
<div class="abs card video">
  <div class="video-frame" role="img" aria-label="Featured video: customer shopping online at a laptop">
    <svg width="28" height="28" viewBox="0 0 28 28"><circle cx="14" cy="14" r="13" fill="#111" stroke="#fff" stroke-width="2"/><path d="M11 8.5 L20 14 L11 19.5Z" fill="#fff"/></svg>
  </div>
</div>

<section class="abs auctions">
  <h2 class="auctions-head">CURRENT AUCTIONS</h2>
  <article class="abs lot" style="top:44px">
    <div class="lot-head real">REAL ESTATE AUCTION</div>
    <div class="lot-photo" role="img" aria-label="Two-storey family house" style="background:linear-gradient(#8fb3d9,#c4a98a 55%,#6f8f4c)"></div>
    <div class="lot-body">
      <div class="lot-title">Vivamus sollicitudin metus</div>
      <div class="lot-meta">Begins: Suspendisse quam leo molestie sed</div>
      <div class="lot-meta"><b>LOCATION:</b>&nbsp; Cum sociis natoque</div>
      <p class="lot-desc">Phasellus felis dolor scelerisque a tempus eget lobortis id libero. Donec scelerisque leo ac risus. Praesent sit amet est. In dictum dolor eu dictum porttitor enim felis viverra mi eget luctus massa purus quis odio.</p>
    </div>
  </article>
  <article class="abs lot" style="top:202px">
    <div class="lot-head estate">ESTATE AUCTION</div>
    <div class="lot-photo" role="img" aria-label="Glass and steel building facade" style="background:linear-gradient(135deg,#1e3f73,#7fa8d8 50%,#1d3559)"></div>
    <div class="lot-body">
      <div class="lot-title">Vivamus sollicitudin metus</div>
      <div class="lot-meta">Begins: Suspendisse quam leo molestie sed</div>
      <div class="lot-meta"><b>LOCATION:</b>&nbsp; Cum sociis natoque</div>
      <p class="lot-desc">Phasellus felis dolor scelerisque a tempus eget lobortis id libero. Donec scelerisque leo ac risus. Praesent sit amet est. In dictum dolor eu dictum porttitor enim felis viverra mi eget luctus massa purus quis odio.</p>
    </div>
  </article>
  <article class="abs lot" style="top:362px">
    <div class="lot-head auto">AUTOMOBILE AUCTION</div>
    <div class="lot-photo" role="img" aria-label="Driver seated in a new car" style="background:linear-gradient(120deg,#c8d3dc,#8a9aa6 55%,#e3e7ea)"></div>
    <div class="lot-body">
      <div class="lot-title">Vivamus sollicitudin metus</div>
      <div class="lot-meta">Begins: Suspendisse quam leo molestie sed</div>
      <div class="lot-meta"><b>LOCATION:</b>&nbsp; Cum sociis natoque</div>
      <p class="lot-desc">Phasellus felis dolor scelerisque a tempus eget lobortis id libero. Donec scelerisque leo ac risus. Praesent sit amet est. In dictum dolor eu dictum porttitor enim felis viverra mi eget luctus massa purus quis odio.</p>
    </div>
  </article>
  <div class="more">VIEW MORE AUCTION</div>
</section>

<aside>
  <form class="abs card signup">
    <h3 class="side-head">Email Sign Up Form</h3>
    <div class="field">Full Name</div>
    <div class="field">Email address</div>
    <div class="field">Phone no.</div>
    <div class="field">City/State</div>
    <div class="field tall">Message</div>
    <div class="submit">SUBMIT</div>
  </form>
  <section class="abs card services">
    <h3 class="services-head">Services We Provide</h3>
    <ul>
      <li>Cum sociis natoque penatibus</li>
      <li>Et magnis dis parturient montes</li>
      <li>Nascetur ridiculus mus.</li>
      <li>In iaculis facilisis massa.</li>
      <li>Etiam eu urna.</li>
      <li>Suspendisse quam leo</li>
      <li>Nascetur ridiculus mus.</li>
      <li>In iaculis facilisis massa.</li>
      <li>Nascetur ridiculus mus.</li>
      <li>In iaculis facilisis</li>
    </ul>
  </section>
  <div class="abs card partners">
    <span class="partner" style="width:40px"></span>
    <span class="partner" style="width:34px"></span>
    <span class="partner" style="width:70px"></span>
  </div>
</aside>

<footer>
  <div class="abs footer"></div>
  <div class="abs footer-links">Home<span>|</span>Auctions<span>|</span>Services<span>|</span>For Sale<span>|</span>About Us<span>|</span>Ned Videos<span>|</span>News &amp; Events<span>|</span>Contact Us</div>
  <div class="abs footer-copy">© 2014 Company Name. &nbsp;All right reserved. &nbsp;Term of Use</div>
  <div class="abs social">
    <span style="background:#c4302b"></span>
    <span style="background:#3b5998"></span>
    <span style="background:#f26522"></span>
  </div>
</footer>

</body>
</html>
```